Website Design for a holiday home letting busines

We require a redesign of our present website www.pinebrookstays.com. We want the website to stand out and look professional and clean to make holiday hunters want to book a caravan or lodge holiday with us. Our logo is red however we DO NOT want the website to be red. We want a natural colour scheme.

The final design should communicate that we are a professional company to book with.

On the home page we require;
Overview of company
Photo
Search box for holiday (check in)
Late Deals
Reviews
News

We would like the following pages designed; home page, available dates page, caravans page, content page.

The website should be responsive for smart phones. One website I do like is http://www.verdoliso.be/nl/

Target Market(s)

Families

Industry/Entity Type

Travel

Number of Pages Required

5+ page

Font styles to use
Serif

Requirements
Must have
• The project must be responsive for mobile phones and tablets.
• Ability to search for holiday home holidays
• We want a natural colour scheme.
Nice to have
• A style we like is http://www.verdoliso.be/nl/
Should not have
• Do not use red as a colour for the website. Our logo is red so this is the only time we want this used.

```html
<!DOCTYPE html>
<html lang="en">
<head>
<meta charset="utf-8">
<title>Pinebrook Stays – Lodge & Caravan Holidays</title>
<link href="https://fonts.googleapis.com/css2?family=Oswald:wght@400;500;600&family=Open+Sans:ital,wght@0,400;0,600;0,700;1,400&display=swap" rel="stylesheet">
<style>
:root{
  --ink:#333;
  --muted:#7b7b7b;
  --line:#dcdcd6;
  --page:#f1f1ee;
  --white:#fff;
  --nav:#3b3d3a;
  --green:#56793a;
  --green-dark:#3f5c2a;
  --blue:#2a72b5;
  --orange:#e8872b;
  --footer:#2f302e;
  --footer-deep:#232422;
  --brand-red:#c8262c;
  --form:#ebeee6;
}
*{box-sizing:border-box;margin:0;padding:0}
html,body{width:710px;height:1200px;overflow:hidden}
body{background:var(--page);font-family:"Open Sans",Arial,sans-serif;color:var(--ink);position:relative}
.abs{position:absolute}
h2,.heading{font-family:"Oswald",Arial,sans-serif;font-weight:500;text-transform:uppercase;letter-spacing:.3px}

/* header */
.site-header{left:0;top:0;width:710px;height:62px;background:var(--white)}
.brand{left:43px;top:18px;display:flex;align-items:center;gap:6px}
.brand-square{width:16px;height:16px;background:var(--brand-red)}
.brand-name{font-family:"Open Sans",sans-serif;font-weight:700;font-size:15px;color:var(--ink)}
.contact{left:392px;top:16px;font-size:9px;line-height:14px}
.contact .phone{font-weight:700;font-size:11px;color:var(--green-dark);display:flex;align-items:center;gap:4px}
.contact .email{color:var(--muted);padding-left:14px}
.live-chat{left:590px;top:18px;width:78px;height:22px;background:var(--blue);color:#fff;font-family:"Oswald",sans-serif;font-size:10px;display:flex;align-items:center;justify-content:center;letter-spacing:.5px}

.main-nav{left:0;top:62px;width:710px;height:20px;background:var(--nav)}
.main-nav ul{list-style:none;display:flex;gap:17px;padding-left:52px;height:20px;align-items:center}
.main-nav li{color:#e6e6e2;font-size:7.5px}
.main-nav li.active{color:#fff;font-weight:700}

/* hero */
.hero{left:0;top:82px;width:710px;height:266px;background:linear-gradient(180deg,#a9c6dc 0%,#cfdfe6 38%,#8aa86a 62%,#5d7f3c 100%)}
.hero-shade{left:0;top:82px;width:710px;height:266px;background:rgba(0,0,0,.28)}
.hero-title{left:43px;top:178px;font-family:"Oswald",sans-serif;font-size:30px;color:#fff;font-weight:600;letter-spacing:1px}
.hero-sub{left:43px;top:218px;font-family:"Oswald",sans-serif;font-size:13px;color:#f3f0d6;line-height:17px}
.hero-btn{left:43px;top:260px;width:74px;height:18px;background:var(--blue);color:#fff;font-size:7.5px;font-weight:700;display:flex;align-items:center;justify-content:center}
.newsletter{left:500px;top:220px;width:168px;height:86px;background:rgba(40,50,35,.55);padding:9px 10px;color:#fff}
.newsletter .heading{font-size:13px;line-height:15px}
.newsletter .field{margin-top:8px;height:14px;background:#fff}
.newsletter .go{margin-top:6px;width:64px;height:14px;background:var(--orange);font-size:6.5px;font-weight:700;display:flex;align-items:center;justify-content:center;margin-left:auto}

/* popup */
.promo{left:180px;top:112px;width:336px;height:196px;background:var(--white);box-shadow:0 4px 18px rgba(0,0,0,.35);padding:10px 12px}
.promo .heading{font-size:16px;color:var(--blue)}
.promo .lead{font-size:7.5px;color:var(--muted);margin-top:2px}
.promo-photo{position:absolute;left:12px;top:52px;width:312px;height:132px;background:linear-gradient(180deg,#9fc3e2 0%,#c8dcea 45%,#86b060 75%,#628a3f 100%)}
.promo-input{position:absolute;left:144px;top:42px;width:100px;height:16px;background:#fff}
.promo-submit{position:absolute;left:248px;top:42px;width:48px;height:16px;background:var(--orange);color:#fff;font-size:6.5px;font-weight:700;display:flex;align-items:center;justify-content:center}
.promo-close{left:508px;top:104px;width:16px;height:16px;border-radius:50%;background:var(--nav);color:#fff;font-size:9px;display:flex;align-items:center;justify-content:center}

/* main column */
.booking{left:43px;top:362px;width:420px;height:82px;background:var(--form)}
.booking-bar{height:18px;background:var(--green);color:#fff;font-family:"Oswald",sans-serif;font-size:9px;padding-left:10px;display:flex;align-items:center;text-transform:uppercase}
.booking-row{display:flex;align-items:center;gap:6px;padding:8px 10px 0}
.booking label{font-size:7px;font-weight:700;color:var(--ink);text-transform:uppercase}
.select{height:16px;background:#fff;border:1px solid var(--line);font-size:6.5px;color:var(--muted);display:flex;align-items:center;padding-left:5px}
.search-btn{height:16px;width:64px;background:var(--blue);color:#fff;font-size:7px;font-weight:700;display:flex;align-items:center;justify-content:center;gap:3px}

.section-head{font-size:14px;color:var(--green-dark);border-bottom:1px solid var(--line);padding-bottom:3px;width:420px}
.about{left:43px;top:458px;width:420px}
.about p{font-size:7px;line-height:11px;color:var(--muted);margin-top:7px}

.cards{display:flex;gap:18px;margin-top:10px}
.card{width:128px;position:relative}
.card .thumb{height:62px;background:linear-gradient(160deg,#c9b79a,#8c7559)}
.card .thumb.lodge{background:linear-gradient(160deg,#d9cdb6,#9c8466)}
.card .thumb.room{background:linear-gradient(160deg,#e6dccb,#a48c6c)}
.card h3{font-family:"Open Sans",sans-serif;font-size:8.5px;font-weight:700;color:var(--ink);margin-top:6px;width:92px}
.card p{font-size:6px;line-height:8.5px;color:var(--muted);width:92px;margin-top:1px}
.price{position:absolute;right:2px;top:68px;width:30px;height:30px;border-radius:50%;background:var(--blue);color:#fff;font-size:5.5px;line-height:7px;text-align:center;display:flex;flex-direction:column;justify-content:center;font-weight:700}
.caravans{left:43px;top:560px}
.deals{left:43px;top:736px}

/* sidebar */
.sidebar{left:486px;top:362px;width:182px}
.side-head{font-size:13px;color:var(--green-dark);border-bottom:1px solid var(--line);padding-bottom:3px}
.review{margin-top:9px;font-size:6.5px;line-height:9.5px}
.review p{font-style:italic;color:var(--muted)}
.review .who{font-weight:700;color:var(--blue);margin-top:2px}
.review .when{color:#a3a39c;font-size:6px}
.more{text-align:right;font-size:6.5px;font-weight:700;color:var(--ink);margin-top:8px;text-transform:uppercase}
.photo-grid{display:grid;grid-template-columns:repeat(3,1fr);gap:4px;margin-top:9px}
.photo-grid div{height:44px;background:linear-gradient(160deg,#d7ccb8,#9a8468)}
.photo-grid div:nth-child(2n){background:linear-gradient(160deg,#c8d4dc,#8a9c78)}
.news-item{margin-top:8px;font-size:7px;line-height:9.5px}
.news-item .title{font-weight:600;color:var(--blue)}
.news-item .when{color:#a3a39c;font-size:6px}

/* footer */
.site-footer{left:0;top:994px;width:710px;height:206px;background:var(--footer);color:#c9c9c4}
.foot-brand{left:43px;top:1014px;display:flex;align-items:center;gap:6px}
.foot-brand .brand-name{color:#fff;font-size:13px}
.foot-copy{left:43px;top:1040px;font-size:6.5px;line-height:10px;color:#a2a29c}
.foot-col{top:1014px;font-size:6.5px;line-height:12px}
.foot-col li{list-style:none}
.badge{left:596px;top:1010px;width:64px;height:64px;border-radius:50%;background:var(--green);border:3px solid #7ea45c}
.social{left:43px;top:1090px;display:flex;gap:5px}
.social span{width:13px;height:13px;background:#555853}
.foot-bottom{left:0;top:1170px;width:710px;height:30px;background:var(--footer-deep);font-size:6px;color:#8d8d87;padding:8px 43px;line-height:8px}
</style>
</head>
<body>

<header class="abs site-header"></header>
<div class="abs brand"><span class="brand-square"></span><span class="brand-name">Pinebrook Stays</span></div>
<div class="abs contact">
  <div class="phone"><svg width="10" height="10" viewBox="0 0 24 24"><path fill="#3f5c2a" d="M6.6 10.8a15.1 15.1 0 0 0 6.6 6.6l2.2-2.2c.3-.3.7-.4 1-.2 1.1.4 2.3.6 3.6.6.6 0 1 .4 1 1V20c0 .6-.4 1-1 1C10.6 21 3 13.4 3 4c0-.6.4-1 1-1h3.5c.6 0 1 .4 1 1 0 1.3.2 2.5.6 3.6.1.3 0 .7-.2 1z"/></svg>01632 555 108</div>
  <div class="email">hello@pinebrookstays.com</div>
</div>
<div class="abs live-chat">LIVE CHAT</div>

<nav class="abs main-nav">
  <ul>
    <li class="active">Home</li><li>News</li><li>Reviews</li><li>Caravans &amp; Lodges</li><li>2016 Holidays</li><li>Late Deals</li><li>Our Park</li><li>Local Attractions</li><li>Contact Us</li>
  </ul>
</nav>

<div class="abs hero" role="img" aria-label="Photo of holiday lodges and caravans on a green park under a blue sky"></div>
<div class="abs hero-shade"></div>
<div class="abs hero-title">PRIVATE HIRE</div>
<div class="abs hero-sub">Quality Lodge &amp; Caravan Hire at<br>Fernhollow Holiday Park</div>
<div class="abs hero-btn">MORE DETAILS</div>
<div class="abs newsletter">
  <div class="heading">Sign up for our<br>newsletter</div>
  <div class="field"></div>
  <div class="go">SUBSCRIBE NOW</div>
</div>

<div class="abs promo">
  <div class="heading">Popular promotion!</div>
  <div class="lead">Autumn • 3 + 1 free! 3 nights stay in bed &amp; breakfast from £ 99 p.p.</div>
  <div class="promo-photo" role="img" aria-label="Photo of a smiling family outdoors on a sunny day">
    <div class="promo-input"></div>
    <div class="promo-submit">SUBMIT</div>
  </div>
</div>
<div class="abs promo-close">✕</div>

<section class="abs booking">
  <div class="booking-bar">Book your holiday</div>
  <div class="booking-row">
    <label>Check in</label><div class="select" style="width:120px">Select dates</div>
    <label style="margin-left:10px">Check out</label><div class="select" style="width:120px">Select dates</div>
  </div>
  <div class="booking-row">
    <label>Type</label><div class="select" style="width:70px">Select type</div>
    <label style="margin-left:6px">No. of nights</label><div class="select" style="width:70px">Select</div>
    <div class="search-btn"><svg width="7" height="7" viewBox="0 0 24 24"><circle cx="10" cy="10" r="7" fill="none" stroke="#fff" stroke-width="3"/><path d="M15 15l7 7" stroke="#fff" stroke-width="3"/></svg>SEARCH</div>
  </div>
</section>

<section class="abs about">
  <h2 class="section-head">About our company</h2>
  <p>Pinebrook Stays is an independent family business offering quality lodge and caravan holidays at Fernhollow Holiday Park. Our homes are cleaned and checked before every stay, fully equipped and set in peaceful green surroundings. Whether you want a short break or a full week away, we make booking simple, fair and friendly. Families return to us year after year for the relaxed pace, the countryside views and the wide choice of park facilities close by.</p>
</section>

<section class="abs caravans">
  <h2 class="section-head">Caravans and lodges</h2>
  <div class="cards">
    <div class="card"><div class="thumb" role="img" aria-label="Photo of a caravan lounge"></div><h3>New Meadow</h3><p>Three bedrooms, sleeps up to eight guests</p><div class="price">From<br>£299</div></div>
    <div class="card"><div class="thumb lodge" role="img" aria-label="Photo of a lodge kitchen"></div><h3>New Meadow</h3><p>Two bedrooms, sleeps up to six guests</p><div class="price">From<br>£249</div></div>
    <div class="card"><div class="thumb room" role="img" aria-label="Photo of a lodge bedroom"></div><h3>New Meadow</h3><p>Two bedrooms, decking and sea views</p><div class="price">From<br>£279</div></div>
  </div>
</section>

<section class="abs deals">
  <h2 class="section-head">Late deals</h2>
  <div class="cards">
    <div class="card"><div class="thumb room" role="img" aria-label="Photo of a caravan living area"></div><h3>The Juniper</h3><p>Friday 25 September 2015 (3 nights)</p><div class="price">Book<br>£199</div></div>
    <div class="card"><div class="thumb" role="img" aria-label="Photo of a caravan dining area"></div><h3>The Juniper</h3><p>Friday 02 October 2015 (3 nights)</p><div class="price">Book<br>£189</div></div>
    <div class="card"><div class="thumb lodge" role="img" aria-label="Photo of a lodge lounge"></div><h3>The Juniper</h3><p>Friday 09 October 2015 (4 nights)</p><div class="price">Book<br>£219</div></div>
  </div>
</section>

<aside class="abs sidebar">
  <h2 class="side-head">Latest reviews</h2>
  <div class="review"><p>"A spotless caravan and a warm welcome. The kids loved the park and we are already planning our next stay."</p><div class="who">Clara Bentley</div><div class="when">Stayed in New Meadow</div></div>
  <div class="review"><p>"Everything we needed was there. Quiet, clean and easy to book. Great value for a family week away."</p><div class="who">Clara Bentley</div><div class="when">Stayed in New Meadow</div></div>
  <div class="review"><p>"Lovely lodge with a lovely view. Friendly owners who answered every question quickly. Highly recommended."</p><div class="who">Clara Bentley</div><div class="when">Stayed in The Juniper</div></div>
  <div class="more">Read all reviews ›</div>

  <h2 class="side-head" style="margin-top:22px">Photo</h2>
  <div class="photo-grid">
    <div role="img" aria-label="Photo of a caravan interior"></div>
    <div role="img" aria-label="Photo of caravans on the park"></div>
    <div role="img" aria-label="Photo of a lodge exterior"></div>
    <div role="img" aria-label="Photo of a lodge bedroom"></div>
    <div role="img" aria-label="Photo of a caravan by the lawn"></div>
    <div role="img" aria-label="Photo of a caravan kitchen"></div>
  </div>
  <div class="more">View all photos ›</div>

  <h2 class="side-head" style="margin-top:26px">Latest news</h2>
  <div class="news-item"><div class="title">Fireworks Weekend</div><div class="when">Posted on 12 August 2015</div></div>
  <div class="news-item"><div class="title">Go Go Show Live at Fernhollow Park</div><div class="when">Posted on 04 August 2015</div></div>
  <div class="news-item"><div class="title">Seaside Walk Season Opens</div><div class="when">Posted on 28 July 2015</div></div>
  <div class="news-item"><div class="title">Easter With Family Fun Days</div><div class="when">Posted on 15 July 2015</div></div>
  <div class="more">Read all news ›</div>
</aside>

<footer class="abs site-footer"></footer>
<div class="abs foot-brand"><span class="brand-square"></span><span class="brand-name">Pinebrook Stays</span></div>
<div class="abs foot-copy">Copyright © 2015<br>All rights reserved · Privacy Policy</div>
<ul class="abs foot-col" style="left:220px"><li>About us</li><li>News</li><li>Caravans &amp; Lodges</li><li>2016 Holidays</li><li>Late Deals</li></ul>
<ul class="abs foot-col" style="left:320px"><li>Our Park</li><li>Local Attractions</li><li>Reviews</li><li>Contact us</li><li>Photo Gallery</li></ul>
<ul class="abs foot-col" style="left:430px"><li>Frequent Questions</li><li>Park Facilities</li><li>Terms &amp; Conditions</li><li>Booking Terms</li></ul>
<div class="abs badge"></div>
<div class="abs social"><span></span><span></span><span></span><span></span></div>
<div class="abs foot-bottom">© 2015 Pinebrook Stays · Holiday lodges and caravans at Fernhollow Holiday Park · Website terms and cookie policy</div>

</body>
</html>
```